Trailhead Cove Website - Sell Outdoor product

We are a mom and pop company that just opened our website.

We need a fresh, professional, and nice looking website for our outdoor products. We sell hunting, camping, fishing, and hiking products/accessories to name a few. Some of these products are optics, gun safes, gun bi-pods and tripods, gun lights, hunting camera, tents, hearing protection, targets, fishing poles, and hiking backpacks to name a few.

Our current website is: http://www.trailheadcove-example.com . You'll see our logo on the website, and it is attached. We aren't married to this logo, so if the designer thinks they can modify it or even come up with a better design for the website, they are more than welcome to do so. We need someone with good images of their own (clip art and/or outdoor images) they can use if they need to for our website.

I also attached a idea I had in plandraw, but please don't think this is set in stone. It is just a very rough idea. You can also go to our bazarro site to see what we sell: www.bazarro-example.com/shops/k9qz311mrtxn4p . Right now we sell everything on Bazarro, but our website will just focus on outdoor product. So please make it an outdoor focused website. And you can be creative with some of the product category names. We also want to leave room for some parallel product in the future. Like garden tools, back yard furniture, and BBQs.

Our company also wants to include a deals section on the website. We will probably update it once a week or month. I have included what I did for a deal and accompanying images for it. Image is called Morvelid (And the main images are 01 and 02).

We also want to make sure the file is compatible with our current web-hosting company, https://www.hostlyne-example.com. So I included a webpage layout zip folder. If you have any questions, please contact me.

This is for a PSD and HTML/CSS webpage. If you have any artwork or images that you own and want to use them for the webpage, please do so.

Target Market(s)

The hunter, outdoors person, camper, hiker, and etc.

Industry/Entity Type

It Company

Coding

Coded - Design and coding required

Number of Pages Required

3 page

Requirements
Must have
• The main page. PSD and HTML/CSS file.
• The category page. PSD and HTML/CSS file
• The product display page. PSD and HTML/CSS file
• Please also use some images that you have or from the sites below:
• You can get free stock images for 7 days (20 per day) from this site:
• https://www.pixelvault-example.com/complimentary/PVXTRL/?utm_source=PVXTrialFT&utm_medium=cpc&utm_campaign=PVXTrialFT&gclid=QWRt5mnBkdTRZpLoWsePb7uVbQ
• Has 14 good sites:
• http://www.venturedesk-example.com/article/517293
• Here are the ones I like:
• https://clearshot-example.com/
• http://brightwide-example.com/
• http://www.sitebloom-example.com/free/nature
• http://www.pictorium-example.com/archive
• http://tinyframes-example.co/
• http://old.vintlens-example.co/search/hiking
• http://fetchpix.blogsite-example.com/
• http://rolvenpask-example.com/post/584920173645/download
• http://openimagevault-example.com/
• If there is a photographer listed on or next to the image, on the bottom lower corner of the image, please put the photographer's name.
Nice to have
• I would like to have an unsubscribe page. If the designer has any of their own images of the outdoor world, and they want to use them, please do. Just make the right graphic changes to make it look good.
Should not have
• Try and keep green color to a minimum.

```html
<!DOCTYPE html>
<html lang="en">
<head>
<meta charset="utf-8">
<title>Trailhead Cove</title>
<link href="https://fonts.googleapis.com/css2?family=Oswald:wght@400;600&family=Open+Sans:wght@400;600;700&display=swap" rel="stylesheet">
<style>
:root{
  --ink:#222;
  --dark:#1d1d1d;
  --darker:#141414;
  --accent:#8dc63f;
  --orange:#f7a823;
  --red:#d8262b;
  --line:#e3e3e3;
  --muted:#8a8a8a;
  --page:#ffffff;
  --soft:#f4f4f4;
}
*{box-sizing:border-box;margin:0;padding:0}
html,body{width:1200px;height:2232px;overflow:hidden}
body{background:var(--page);font-family:"Open Sans",Arial,sans-serif;color:var(--ink);position:relative}
.wrap{position:absolute;left:100px;width:1004px}

/* top bar */
.topbar{position:absolute;top:0;left:0;width:1200px;height:56px;background:var(--dark)}
.topbar .currency{position:absolute;left:100px;top:14px;width:100px;height:26px;background:#fff;border-radius:2px;font-size:11px;line-height:26px;padding-left:8px;color:#555}
.topbar .links{position:absolute;left:720px;top:0;line-height:56px;font-size:12px;color:#ddd}
.topbar .links span{margin-right:34px}
.topbar .links svg{vertical-align:-2px;margin-right:6px}
.topbar .search{position:absolute;left:920px;top:14px;width:104px;height:26px;background:#fff;border-radius:2px;font-size:11px;line-height:26px;padding-left:8px;color:#777}
.topbar .cart{position:absolute;left:1032px;top:12px;width:96px;height:30px;background:var(--accent);color:#fff;font-size:12px;font-weight:600;line-height:30px;text-align:center;border-radius:2px}

.brand{position:absolute;left:100px;top:56px;height:100px;width:220px;display:flex;align-items:center;gap:10px}
.brand .mark{width:34px;height:34px;background:var(--orange);border-radius:50%;flex:none}
.brand .name{font-family:"Oswald",sans-serif;font-weight:600;font-size:30px;line-height:1;color:var(--ink);text-transform:uppercase}

/* nav */
.nav{top:168px;height:34px;background:var(--soft);border-bottom:1px solid var(--line);display:flex;font-size:12px;font-weight:600}
.nav a{display:block;padding:0 42px;line-height:34px;color:#333;text-decoration:none}
.nav a.active{background:var(--accent);color:#fff;padding:0 24px}

/* sidebar */
.sidebar{position:absolute;left:100px;top:212px;width:288px;height:588px;background:#fff;border:1px solid var(--line)}
.sidebar h3{background:var(--accent);color:#fff;font-size:12px;font-weight:700;height:46px;line-height:46px;padding-left:58px;letter-spacing:.3px;position:relative}
.sidebar h3::before{content:"";position:absolute;left:22px;top:15px;width:18px;height:2px;background:#fff;box-shadow:0 6px 0 #fff,0 12px 0 #fff}
.sidebar ul{list-style:none}
.sidebar li{height:60px;line-height:60px;border-bottom:1px solid var(--line);padding-left:58px;font-size:11px;font-weight:700;color:#333;position:relative}
.sidebar li::before{content:"";position:absolute;left:22px;top:22px;width:16px;height:16px;border-radius:50%;background:#666}
.sidebar li::after{content:"›";position:absolute;right:18px;color:#aaa;font-size:16px}

/* hero */
.hero{position:absolute;left:400px;top:212px;width:704px;height:588px;background:linear-gradient(180deg,#1a3a5e 0%,#3e5b7c 40%,#e6914a 72%,#2a2018 74%,#0e0c0a 100%)}
.hero h1{position:absolute;left:0;width:100%;top:118px;text-align:center;color:#fff;font-family:"Oswald",sans-serif;font-weight:400;font-size:44px}
.hero p{position:absolute;left:230px;width:244px;top:188px;text-align:center;color:#e8ecf2;font-size:12px;line-height:18px}
.hero .dots{position:absolute;left:0;width:100%;bottom:22px;text-align:center}
.hero .dots i{display:inline-block;width:9px;height:9px;border-radius:50%;background:#fff;opacity:.55;margin:0 4px}
.hero .dots i:first-child{opacity:1}

/* search */
.searchbar{top:846px;height:56px;background:var(--soft);border:1px solid var(--line)}
.searchbar span{position:absolute;left:70px;line-height:54px;font-size:14px;color:#888}
.searchbar .go{position:absolute;right:0;top:0;width:110px;height:54px;background:var(--accent);color:#fff;font-family:"Oswald",sans-serif;font-size:22px;text-align:center;line-height:54px}

/* sections */
.section-title{font-family:"Oswald",sans-serif;font-weight:600;font-size:28px;color:var(--ink);height:40px;border-bottom:1px solid var(--line)}
.section-title .arrows{position:absolute;right:0;top:8px;display:flex;gap:6px}
.section-title .arrows i{width:22px;height:22px;background:#ddd;display:block}
.grid{position:absolute;left:0;width:1004px;display:flex;gap:16px}
.card{width:188px;background:#fff;border:1px solid var(--line);position:relative;text-align:center}
.card .photo{margin:26px 20px 0;height:150px;background:radial-gradient(circle at 50% 50%,#4a4a4a 0%,#1e1e1e 45%,#fff 70%)}
.card .photo.tent{background:radial-gradient(circle at 50% 55%,#6fa84a 0%,#3e6e2a 40%,#fff 68%)}
.card .photo.ear{background:radial-gradient(circle at 50% 50%,#2f6bb3 0%,#15365e 45%,#fff 70%)}
.card .photo.ammo{background:linear-gradient(90deg,#fff 0%,#fff 10%,#b8892e 30%,#d8ad55 60%,#6b4a18 88%,#fff 100%);height:40px;margin:78px 20px 32px}
.card .title{font-size:11px;margin-top:16px;color:#333}
.card .price{font-size:15px;font-weight:700;margin-top:6px}
.card .label{font-size:10px;color:var(--muted);margin-top:4px}
.card .tag{position:absolute;left:-1px;top:-1px;background:var(--dark);color:#fff;font-size:9px;font-weight:700;padding:4px 8px}
.card .ribbon{position:absolute;right:-1px;top:-1px;width:0;height:0;border-top:46px solid var(--red);border-left:46px solid transparent}
.card.featured{box-shadow:0 4px 18px rgba(0,0,0,.22);z-index:2}
.card .off{position:absolute;right:-1px;top:-1px;background:var(--orange);color:#fff;font-size:11px;font-weight:700;padding:6px 10px}
.card .stars{color:var(--orange);font-size:12px;letter-spacing:1px;margin-top:4px}
.card .btns{display:flex;gap:6px;justify-content:center;margin-top:12px}
.card .btns span{font-size:10px;font-weight:700;color:#fff;padding:7px 12px;border-radius:2px}
.card .btns .add{background:var(--accent)}
.card .btns .buy{background:var(--orange)}
.card .meta{border-top:1px solid var(--line);margin-top:14px;display:flex;justify-content:space-around;font-size:9px;color:var(--muted);line-height:30px}

/* footer */
.footer{position:absolute;left:0;top:1886px;width:1200px;height:272px;background:var(--dark)}
.footer .cols{position:absolute;left:100px;top:32px;width:1004px;display:flex;gap:30px}
.footer .col{width:229px;color:#aaa;font-size:9px;line-height:16px}
.footer h4{color:#fff;font-family:"Oswald",sans-serif;font-weight:400;font-size:15px;margin-bottom:12px;letter-spacing:.5px}
.footer ul{list-style:none}
.footer li::before{content:"› ";color:var(--accent)}
.footer .hl{color:var(--accent)}
.bottombar{position:absolute;left:0;top:2158px;width:1200px;height:74px;background:var(--darker);color:#888;font-size:9px}
.bottombar .copy{position:absolute;left:100px;top:30px}
.bottombar .help{position:absolute;right:96px;top:18px;color:#ddd;font-size:12px}
.bottombar .help b{color:var(--accent)}
.bottombar .menu{position:absolute;right:96px;top:40px}
.bottombar .menu span{margin-left:12px}
</style>
</head>
<body>

<header class="topbar">
  <div class="currency">Australian ▾</div>
  <div class="links">
    <span><svg width="11" height="11" viewBox="0 0 11 11"><circle cx="5.5" cy="3.5" r="2.5" fill="#ddd"/><path d="M1 11c0-3 2-4.5 4.5-4.5S10 8 10 11z" fill="#ddd"/></svg>My Account</span>
    <span><svg width="11" height="11" viewBox="0 0 11 11"><rect x="1" y="5" width="9" height="6" fill="#ddd"/><path d="M3 5V3.5a2.5 2.5 0 0 1 5 0V5" stroke="#ddd" fill="none" stroke-width="1.4"/></svg>Login</span>
  </div>
  <div class="search">Search</div>
  <div class="cart">Purchase</div>
</header>

<div class="brand"><span class="mark"></span><span class="name">Trailhead<br>Cove</span></div>

<nav class="wrap nav">
  <a class="active">Home</a><a>Hunting/accessories</a><a>Camping</a><a>Fishing</a><a>Hiking</a><a>This week deals</a><a>Brands</a>
</nav>

<aside class="sidebar">
  <h3>SHOP ALL CATEGORIES</h3>
  <ul>
    <li>OPTICS</li><li>SAFES</li><li>BIPOD AND TRIPODS</li><li>LIGHTS</li><li>CAMERA</li><li>TENTS</li><li>EAR PROTECTION</li><li>TARGETS</li>
  </ul>
</aside>

<section class="hero" role="img" aria-label="Hiker silhouetted on a hilltop against a sunset sky">
  <h1>Trailhead Cove</h1>
  <p>Lorem ipsum is simply dummy text of the printing and typesetting industry.</p>
  <div class="dots"><i></i><i></i><i></i><i></i></div>
</section>

<div class="wrap searchbar"><span>Search for Products</span><div class="go">GO</div></div>

<section class="wrap" style="top:962px">
  <div class="section-title">RECENT PRODUCTS<div class="arrows"><i></i><i></i></div></div>
  <div class="grid" style="top:76px;align-items:flex-start">
    <div class="card" style="height:300px"><span class="tag">NEW</span><div class="photo" role="img" aria-label="Black keypad gun safe"></div><div class="title">Keypad Pistol Safe</div><div class="price">$ 33.99</div><div class="label">Text label</div></div>
    <div class="card featured" style="height:362px;margin-top:-12px"><span class="tag">NEW</span><span class="off">10% off</span><div class="photo ammo" role="img" aria-label="Brass rifle cartridge"></div><div class="title">Party Favourite</div><div class="price">$ 33.99</div><div class="stars">★★★★★</div><div class="btns"><span class="add">Add to Cart</span><span class="buy">Buy Now</span></div><div class="meta"><span>♡ Wishlist</span><span>⇄ Compare</span><span>↗ Share</span></div></div>
    <div class="card" style="height:300px"><span class="tag">NEW</span><div class="photo" role="img" aria-label="Rifle scope"></div><div class="title">Hunting Riflescope</div><div class="price">$ 33.99</div><div class="label">Text label</div></div>
    <div class="card" style="height:300px"><span class="tag">NEW</span><div class="photo ear" role="img" aria-label="Hearing protection ear muffs"></div><div class="title">Shooting Ear Muffs</div><div class="price">$ 33.99</div><div class="label">Text label</div></div>
    <div class="card" style="height:300px"><span class="tag">NEW</span><div class="photo" role="img" aria-label="Hunting trail camera"></div><div class="title">Compact Trail Camera</div><div class="price">$ 33.99</div><div class="label">Text label</div></div>
  </div>
</section>

<section class="wrap" style="top:1420px">
  <div class="section-title">NEW ARRIVALS<div class="arrows"><i></i><i></i></div></div>
  <div class="grid" style="top:76px">
    <div class="card" style="height:290px"><span class="tag">NEW</span><span class="ribbon"></span><div class="photo" role="img" aria-label="Trail camera"></div><div class="title">Low Glow Trail Camera</div><div class="price">$ 33.99</div><div class="label">Text label</div></div>
    <div class="card" style="height:290px"><span class="tag">NEW</span><span class="ribbon"></span><div class="photo tent" role="img" aria-label="Green dome tent"></div><div class="title">Four Person Dome Tent</div><div class="price">$ 33.99</div><div class="label">Text label</div></div>
    <div class="card" style="height:290px"><span class="tag">NEW</span><span class="ribbon"></span><div class="photo" role="img" aria-label="Red dot sight"></div><div class="title">Red Dot Reflex Sight</div><div class="price">$ 33.99</div><div class="label">Text label</div></div>
    <div class="card" style="height:290px"><span class="tag">NEW</span><span class="ribbon"></span><div class="photo" role="img" aria-label="Tactical rifle bipod"></div><div class="title">Tactical Rifle Bipod</div><div class="price">$ 33.99</div><div class="label">Text label</div></div>
    <div class="card" style="height:290px"><span class="tag">NEW</span><span class="ribbon"></span><div class="photo ear" role="img" aria-label="Shooting target stand"></div><div class="title">Steel Target Stand Kit</div><div class="price">$ 33.99</div><div class="label">Text label</div></div>
  </div>
</section>

<footer class="footer">
  <div class="cols">
    <div class="col"><h4>ABOUT US</h4><p>Outdoor gear for hunters, campers, anglers and hikers. A small family shop that tests every product in the field before it reaches your door.</p></div>
    <div class="col"><h4>TERMS &amp; CONDITIONS</h4><ul><li>Shipping &amp; Terms</li><li>Returnable Items</li><li>Policies</li><li>Affiliates</li><li>Legal Notice</li><li>Privacy &amp; Security</li><li>Sitemap</li></ul></div>
    <div class="col"><h4>CONTACT US</h4><p>Trailhead Cove Outdoor<br>12 Ridge Road, Pinewood Valley<br><span class="hl">Tel:</span> (123) 456-7890<br><span class="hl">Email:</span> hello@trailheadcove-example.com<br>Mon - Fri, 9am to 5pm</p></div>
    <div class="col"><h4>SHIPPING AND RETURN</h4><p>All orders ship within two business days. Items may be returned within thirty days in their original packaging for a full refund.</p></div>
  </div>
</footer>
<div class="bottombar">
  <div class="copy">© 2024 Trailhead Cove. All rights reserved.</div>
  <div class="help">Need help? <b>(123) 456-7890</b></div>
  <div class="menu"><span>Home</span><span>About Us</span><span>FAQ</span><span>Blog</span><span>Shipping</span><span>Contact</span></div>
</div>

</body>
</html>
```